Business Card Design

We need a business card designed for our new company. Prefer a black card with white logo & writing.

Contact Information for Business Card

Ted Galloway, address: 7-4812 Fernhollow Road, Abbotsford, BC, V3K 8R2, Office Phone: 604-712-3390, Cell: 604-947-2164, Email: ted@resinworkshub.ca

Colors

Designer to choose only greyscale colors for use in the design.

```html
<!DOCTYPE html>
<html lang="en">
<head>
<meta charset="utf-8">
<title>Resinworks Hub — Business Card</title>
<link href="https://fonts.googleapis.com/css2?family=Montserrat:wght@400;600;700&display=swap" rel="stylesheet">
<style>
  :root {
    --bg: #2b2b2b;
    --card: #141414;
    --white: #ffffff;
    --soft-grey: #d9d9d9;
    --mid-grey: #8a8a8a;
    --text-grey: #555555;
  }
  * { margin: 0; padding: 0; box-sizing: border-box; }
  html, body {
    width: 1200px; height: 1059px; overflow: hidden;
    background: var(--bg);
    font-family: "Montserrat", sans-serif;
    color: var(--white);
  }
  .canvas { position: relative; width: 1200px; height: 1059px; }
  .card {
    position: absolute;
    background: var(--card);
    border-radius: 22px;
    overflow: hidden;
  }
  .card--front { left: 256px; top: 89px; width: 688px; height: 390px; }
  .card--back { left: 252px; top: 546px; width: 696px; height: 395px; }

  .front-accent {
    position: absolute; left: -148px; top: 0;
    width: 357px; height: 390px;
    border-radius: 0 195px 195px 0;
    background: linear-gradient(90deg, var(--white) 55%, var(--soft-grey));
  }

  .wordmark {
    position: absolute;
    display: flex; flex-direction: column; align-items: center;
    font-weight: 700; color: var(--white); line-height: 1;
  }
  .wordmark__main { letter-spacing: 0.5px; }
  .wordmark__sub { letter-spacing: 8px; margin-top: 10px; }
  .card--front .wordmark { left: 330px; top: 196px; width: 306px; }
  .card--front .wordmark__main { font-size: 38px; }
  .card--front .wordmark__sub { font-size: 20px; }
  .card--back .wordmark { left: 118px; top: 83px; width: 460px; }
  .card--back .wordmark__main { font-size: 30px; }
  .card--back .wordmark__sub { font-size: 16px; }

  .person {
    position: absolute; right: 370px; top: 254px;
    text-align: right;
  }
  .person__name { font-size: 30px; font-weight: 600; line-height: 1.1; }
  .person__title { font-size: 17px; font-weight: 400; margin-top: 6px; }

  .divider {
    position: absolute; left: 354px; top: 245px;
    width: 1.5px; height: 73px; background: var(--white);
  }

  .contacts {
    position: absolute; left: 376px; top: 241px;
    list-style: none; font-size: 18px; font-weight: 400;
  }
  .contacts li { display: flex; align-items: center; height: 27px; }
  .contacts svg { width: 15px; height: 15px; margin-right: 8px; fill: none; stroke: var(--white); stroke-width: 1.6; }

  .address-band {
    position: absolute; left: 0; top: 345px;
    width: 100%; height: 25px;
    background: var(--white);
    color: var(--text-grey);
    font-size: 17px; text-align: center; line-height: 25px;
  }
</style>
</head>
<body>
<div class="canvas">
  <section class="card card--front">
    <div class="front-accent" role="img" aria-label="Large brand decoration area"></div>
    <div class="wordmark">
      <span class="wordmark__main">RESINWORKS</span>
      <span class="wordmark__sub">HUB</span>
    </div>
  </section>

  <section class="card card--back">
    <div class="wordmark">
      <span class="wordmark__main">RESINWORKS</span>
      <span class="wordmark__sub">HUB</span>
    </div>

    <div class="person">
      <p class="person__name">Ted Galloway</p>
      <p class="person__title">Owner/CEO</p>
    </div>
    <div class="divider"></div>

    <ul class="contacts">
      <li>
        <svg viewBox="0 0 16 16"><path d="M2 6c0-2 3-3 6-3s6 1 6 3v1h-3V6H5v1H2z"/><rect x="4" y="8" width="8" height="5" rx="1"/></svg>
        604-712-3390
      </li>
      <li>
        <svg viewBox="0 0 16 16"><rect x="4.5" y="1.5" width="7" height="13" rx="1.5"/><line x1="7" y1="12" x2="9" y2="12"/></svg>
        604-947-2164
      </li>
      <li>
        <svg viewBox="0 0 16 16"><rect x="1.5" y="4" width="13" height="9" rx="1"/><path d="M1.5 4.5 8 9.5l6.5-5"/></svg>
        ted@resinworkshub.ca
      </li>
    </ul>

    <div class="address-band">7-4812 Fernhollow Road, Abbotsford, BC, V3K 8R2</div>
  </section>
</div>
</body>
</html>
```